Letter and Envelope Design For Harborline Realty

Please design a letter and an envelope incorporating our logo (See Attached). We are also launched a business card contest. Since we want them to match, please feel free to submit a design for both the business card and also the letter design and envelope.

Requirements
Must have
• The envelope, the letter and the business cards must match somehow connecting the designs. We want them to have something that holds them together besides the logo.

```html
<!DOCTYPE html>
<html lang="en">
<head>
<meta charset="utf-8">
<title>Harborline Realty – Stationery Set</title>
<link rel="stylesheet" href="https://fonts.googleapis.com/css2?family=Source+Sans+3:wght@400;600&family=Ubuntu:wght@500&display=swap">
<style>
  :root {
    --navy: #283080;
    --charcoal: #555555;
    --ink: #3a3a3a;
    --paper: #ffffff;
    --backdrop: #d4d4d4;
    --label: #222222;
  }
  * { box-sizing: border-box; margin: 0; padding: 0; }
  html, body { width: 1200px; height: 1200px; overflow: hidden; }
  body {
    position: relative;
    background: var(--backdrop);
    font-family: "Source Sans 3", "Helvetica Neue", Arial, sans-serif;
    color: var(--ink);
  }
  .option-label {
    position: absolute; top: 2px;
    font-size: 19px; color: var(--label);
    transform: translateX(-50%);
  }
  .sheet {
    position: absolute;
    background: var(--paper);
    box-shadow: 0 2px 8px rgba(0,0,0,.22);
    overflow: hidden;
  }
  /* brand block: plain circle + name */
  .brand { position: absolute; display: flex; flex-direction: column; align-items: center; transform: translateX(-50%); }
  .brand-circle { border: 3px solid var(--navy); border-radius: 50%; }
  .brand-name {
    color: var(--navy); font-weight: 600; text-align: center;
    letter-spacing: .14em; line-height: 1.15; text-transform: uppercase;
  }
  /* footer band shared by all pieces */
  .band {
    position: absolute; left: 0; right: 0; bottom: 0;
    background: linear-gradient(90deg, var(--navy) 0 var(--split), var(--charcoal) var(--split));
  }
  .band-seal {
    position: absolute; top: 50%;
    background: var(--paper); border-radius: 50%;
    border: 2px solid var(--navy);
    box-shadow: 0 0 0 2px var(--paper);
    transform: translate(-50%, -50%);
  }
  /* contact lines */
  .contact { position: absolute; display: flex; flex-direction: column; }
  .contact-line { display: flex; align-items: center; white-space: nowrap; }
  .contact-line svg { flex: none; }
  .contact-row { display: flex; align-items: center; white-space: nowrap; }

  /* Option 1 letterhead */
  .letter-one { left: 26px; top: 30px; width: 538px; height: 762px; }
  .letter-one .brand { left: 269px; top: 26px; }
  .letter-one .brand-circle { width: 78px; height: 78px; margin-bottom: 10px; }
  .letter-one .brand-name { font-size: 24px; }
  .letter-one .footer-contact {
    position: absolute; left: 0; width: 502px; top: 694px;
    display: flex; flex-direction: column; align-items: center; gap: 5px;
    font-size: 8.5px;
  }
  .letter-one .footer-contact .contact-row { gap: 14px; }
  .letter-one .footer-contact .contact-line { gap: 5px; }
  .letter-one .band { height: 32px; --split: 456px; }
  .letter-one .band-seal { left: 456px; width: 38px; height: 38px; }

  /* Option 2 letterhead */
  .letter-two { left: 600px; top: 38px; width: 528px; height: 746px; }
  .letter-two .brand { left: 98px; top: 22px; }
  .letter-two .brand-circle { width: 58px; height: 58px; margin-bottom: 8px; }
  .letter-two .brand-name { font-size: 16px; }
  .letter-two .contact { left: 366px; top: 40px; gap: 4px; font-size: 8.3px; }
  .letter-two .contact-line { gap: 8px; }
  .letter-two .band { height: 31px; --split: 446px; }
  .letter-two .band-seal { left: 446px; width: 38px; height: 38px; }
  .letter-two .card-back {
    position: absolute; left: 102px; top: 486px; width: 325px; height: 190px;
    background: var(--navy);
    box-shadow: 0 3px 10px rgba(0,0,0,.3);
  }
  .card-back .back-circle {
    position: absolute; left: 50%; top: 50%; width: 48px; height: 48px;
    border: 2px solid var(--paper); border-radius: 50%;
    transform: translate(-50%, -50%);
  }

  /* Envelope */
  .envelope { position: absolute; left: 26px; top: 808px; width: 623px; height: 379px; }
  .envelope .flap { position: absolute; left: 0; top: 0; }
  .envelope-body {
    position: absolute; left: 0; top: 82px; width: 623px; height: 297px;
    background: var(--paper); box-shadow: 0 2px 8px rgba(0,0,0,.22);
  }
  .envelope .brand { left: 98px; top: 14px; }
  .envelope .brand-circle { width: 60px; height: 60px; margin-bottom: 8px; }
  .envelope .brand-name { font-size: 16px; }
  .envelope .contact { left: 470px; top: 26px; gap: 5px; font-size: 8.3px; }
  .envelope .contact-line { gap: 10px; }
  .envelope .band { height: 32px; --split: 540px; }
  .envelope .band-seal { left: 540px; width: 38px; height: 38px; }

  /* Business card */
  .business-card { left: 758px; top: 888px; width: 370px; height: 218px; }
  .business-card .brand { left: 83px; top: 70px; }
  .business-card .brand-circle { width: 46px; height: 46px; margin-bottom: 6px; }
  .business-card .brand-name { font-size: 12.5px; }
  .business-card .divider {
    position: absolute; left: 169px; top: 36px; width: 1px; height: 130px; background: var(--charcoal);
  }
  .business-card .person { position: absolute; left: 185px; top: 28px; }
  .person-name { font-family: "Ubuntu", "Source Sans 3", sans-serif; font-weight: 500; font-size: 19.5px; color: var(--navy); line-height: 1.1; }
  .person-role { font-size: 12px; color: var(--ink); line-height: 1.2; }
  .business-card .contact { left: 182px; top: 91px; gap: 7px; font-size: 11px; }
  .business-card .contact-line { gap: 10px; }
  .business-card .band { height: 21px; --split: 298px; }
  .business-card .band-seal { left: 298px; width: 28px; height: 28px; }
</style>
</head>
<body>

<svg width="0" height="0" style="position:absolute" aria-hidden="true">
  <defs>
    <symbol id="icon-pin" viewBox="0 0 12 12">
      <rect width="12" height="12" fill="#283080"/>
      <path d="M6 2.3a2.3 2.3 0 0 1 2.3 2.3c0 1.7-2.3 4.3-2.3 4.3S3.7 6.3 3.7 4.6A2.3 2.3 0 0 1 6 2.3z" fill="none" stroke="#fff" stroke-width=".9"/>
      <path d="M2.5 9.8h7" stroke="#fff" stroke-width=".9"/>
    </symbol>
    <symbol id="icon-phone" viewBox="0 0 12 12">
      <rect width="12" height="12" fill="#283080"/>
      <path d="M2.3 5.2c0-1.4 1.6-2.2 3.7-2.2s3.7.8 3.7 2.2l-1.6.4-.4-1H4.3l-.4 1z" fill="#fff"/>
      <rect x="3.4" y="6" width="5.2" height="3.3" rx=".5" fill="#fff"/>
    </symbol>
    <symbol id="icon-mail" viewBox="0 0 12 12">
      <rect width="12" height="12" fill="#283080"/>
      <rect x="2.4" y="3.5" width="7.2" height="5" fill="#fff"/>
      <path d="M2.4 3.5 6 6.5l3.6-3" fill="none" stroke="#283080" stroke-width=".8"/>
    </symbol>
    <symbol id="icon-globe" viewBox="0 0 12 12">
      <rect width="12" height="12" fill="#283080"/>
      <circle cx="6" cy="6" r="3.5" fill="none" stroke="#fff" stroke-width=".8"/>
      <ellipse cx="6" cy="6" rx="1.5" ry="3.5" fill="none" stroke="#fff" stroke-width=".7"/>
      <path d="M2.5 6h7" stroke="#fff" stroke-width=".7"/>
    </symbol>
  </defs>
</svg>

<div class="option-label" style="left:288px">Option 1</div>
<div class="option-label" style="left:864px">Option 2</div>

<!-- Option 1 letterhead -->
<section class="sheet letter-one" aria-label="Letterhead, option 1">
  <div class="brand">
    <div class="brand-circle"></div>
    <div class="brand-name">Harborline<br>Realty</div>
  </div>
  <div class="footer-contact">
    <div class="contact-line"><svg width="11" height="11"><use href="#icon-pin"/></svg>Harborline Realty</div>
    <div class="contact-row">
      <div class="contact-line"><svg width="11" height="11"><use href="#icon-phone"/></svg>312-555-0148</div>
      <div class="contact-line"><svg width="11" height="11"><use href="#icon-mail"/></svg>info@harborline-realty.com</div>
      <div class="contact-line"><svg width="11" height="11"><use href="#icon-globe"/></svg>www.harborline-realty.com</div>
    </div>
  </div>
  <div class="band"><div class="band-seal"></div></div>
</section>

<!-- Option 2 letterhead with card back -->
<section class="sheet letter-two" aria-label="Letterhead, option 2">
  <div class="brand">
    <div class="brand-circle"></div>
    <div class="brand-name">Harborline<br>Realty</div>
  </div>
  <div class="contact">
    <div class="contact-line"><svg width="11" height="11"><use href="#icon-pin"/></svg>Harborline Realty</div>
    <div class="contact-line"><svg width="11" height="11"><use href="#icon-phone"/></svg>312-555-0148</div>
    <div class="contact-line"><svg width="11" height="11"><use href="#icon-mail"/></svg>info@harborline-realty.com</div>
    <div class="contact-line"><svg width="11" height="11"><use href="#icon-globe"/></svg>www.harborline-realty.com</div>
  </div>
  <div class="card-back" aria-label="Business card back"><div class="back-circle"></div></div>
  <div class="band"><div class="band-seal"></div></div>
</section>

<!-- Envelope -->
<section class="envelope" aria-label="Envelope">
  <svg class="flap" width="623" height="83" viewBox="0 0 623 83" aria-hidden="true">
    <path d="M0 82 L22 10 Q25 0 36 0 L586 0 Q597 0 600 10 L623 82 Z" fill="var(--navy)"/>
  </svg>
  <div class="envelope-body">
    <div class="brand">
      <div class="brand-circle"></div>
      <div class="brand-name">Harborline<br>Realty</div>
    </div>
    <div class="contact">
      <div class="contact-line"><svg width="11" height="11"><use href="#icon-pin"/></svg>Harborline Realty</div>
      <div class="contact-line"><svg width="11" height="11"><use href="#icon-phone"/></svg>312-555-0148</div>
      <div class="contact-line"><svg width="11" height="11"><use href="#icon-mail"/></svg>info@harborline-realty.com</div>
      <div class="contact-line"><svg width="11" height="11"><use href="#icon-globe"/></svg>www.harborline-realty.com</div>
    </div>
    <div class="band"><div class="band-seal"></div></div>
  </div>
</section>

<!-- Business card front -->
<section class="sheet business-card" aria-label="Business card">
  <div class="brand">
    <div class="brand-circle"></div>
    <div class="brand-name">Harborline<br>Realty</div>
  </div>
  <div class="divider"></div>
  <div class="person">
    <div class="person-name">Daniel Reyes</div>
    <div class="person-role">Realtor</div>
  </div>
  <div class="contact">
    <div class="contact-line"><svg width="14" height="14"><use href="#icon-pin"/></svg>Harborline Realty</div>
    <div class="contact-line"><svg width="14" height="14"><use href="#icon-phone"/></svg>312-555-0148</div>
    <div class="contact-line"><svg width="14" height="14"><use href="#icon-mail"/></svg>info@harborline-realty.com</div>
    <div class="contact-line"><svg width="14" height="14"><use href="#icon-globe"/></svg>www.harborline-realty.com</div>
  </div>
  <div class="band"><div class="band-seal"></div></div>
</section>

</body>
</html>
```